New Dental Office Needs an Attractive and user friendly Website Designed

I need a website for a new dental office. The Name is Harrowfield Dentistry. I would like a Modern design with a user friendly interface and usability.
I would like a landing page, a page that lists the services we offer: Cosmetic Dentistry, Implants, Dental Hygiene, Emergency Services, Restorations, Dentures
Target Market(s)
Mid to upper class
Industry/Entity Type
Dentistry
Coding
Number of Pages Required
1 page
Requirements
Must have
- Landing page that has a scheduling option, Procedures, operating hours, and contact us info
Nice to have
- Appealing design, Soft comforting colors. Easy to navigate page, Modern and professional.

```html
<!DOCTYPE html>
<html lang="en">
<head>
<meta charset="utf-8">
<title>Harrowfield Dentistry</title>
<link href="https://fonts.googleapis.com/css2?family=Poppins:wght@400;500;600&display=swap" rel="stylesheet">
<style>
:root{
  --navy:#1f3a7f;
  --navy-deep:#19306b;
  --teal:#5aacbc;
  --teal-light:#8fc8d3;
  --ink:#1e2433;
  --muted:#6b7280;
  --band:#e8ecf4;
  --footer:#0e1a30;
  --white:#ffffff;
}
*{box-sizing:border-box;margin:0;padding:0}
html,body{width:1200px;height:4622px;overflow:hidden}
body{position:relative;font-family:'Poppins',sans-serif;color:var(--ink);background:var(--white)}
.abs{position:absolute}
.btn{position:absolute;display:flex;align-items:center;justify-content:center;background:var(--teal);color:var(--white);font-size:13px;font-weight:500;border-radius:3px}
.btn-navy{background:var(--navy);font-size:11px;font-weight:500}
.eyebrow{font-size:13px;color:var(--navy);display:flex;align-items:center;gap:10px}
.eyebrow .mark{width:30px;height:30px;border-radius:50%;background:var(--teal-light)}
.eyebrow.light{color:var(--white)}
h2{font-weight:600;font-size:31px;line-height:1.25;color:var(--ink)}
.center{text-align:center;left:0;width:1200px}
.center .eyebrow{justify-content:center}
.lead{font-size:13px;color:var(--muted);line-height:1.5}
.photo{position:absolute}

/* top bar */
.topbar{top:0;left:0;width:1200px;height:36px;background:var(--white);font-size:12px;color:var(--ink)}
.social{display:flex;gap:22px}
.social span{width:12px;height:12px;border-radius:50%;background:var(--navy)}

/* hero */
.hero-photo{top:36px;left:0;width:1200px;height:680px;background:linear-gradient(110deg,#c9a38a 0%,#e8d6c8 30%,#9fb4c9 55%,#3e4f66 100%)}
.nav{top:36px;left:0;width:1200px;height:90px;background:rgba(40,40,40,.72)}
.brand{color:var(--white);font-size:26px;font-weight:500;line-height:1}
.brand small{display:block;font-size:12px;letter-spacing:5px;margin-top:4px;text-align:center}
.nav-links{display:flex;gap:36px;color:var(--white);font-size:14px}
.hero-circle{left:643px;top:183px;width:394px;height:394px;border-radius:50%;background:rgba(31,58,127,.88);color:var(--white);text-align:center;padding-top:115px}
.hero-ring{left:632px;top:172px;width:416px;height:416px;border-radius:50%;border:2px solid rgba(255,255,255,.8)}
.hero-circle h1{font-weight:500;font-size:30px;line-height:1.25}
.hero-circle h1 strong{font-weight:600;font-size:37px;display:block}
.hero-circle p{font-size:13px;line-height:1.35;width:300px;margin:12px auto 0}

/* services */
.service-card{position:absolute;top:1565px;width:213px;height:245px;background:var(--white);border-radius:106px 106px 0 0;text-align:center;padding-top:118px}
.service-card h3{font-size:15px;font-weight:600}
.service-card p{font-size:11px;color:var(--muted);line-height:1.3;margin:8px 18px 0}
.service-photo{position:absolute;top:1477px;width:170px;height:170px;border-radius:50%;border:4px solid var(--white)}
.service-more{top:1832px;display:flex;justify-content:center;gap:12px;font-size:12px;color:var(--white)}
.service-more span{border:1px solid rgba(255,255,255,.5);border-radius:14px;padding:4px 14px}
.service-more span.label{border:none;padding:4px 0;color:#dbe3f3}

/* team */
.member{position:absolute;top:2220px;width:200px;text-align:center}
.member .avatar{width:167px;height:167px;border-radius:50%;margin:0 auto 14px}
.member h3{font-size:15px;font-weight:500}
.member p{font-size:11px;color:var(--muted);margin-top:2px}

/* form */
.field{position:absolute;border-bottom:1px solid rgba(255,255,255,.45);color:var(--white);font-size:12px;height:40px}
.hours{left:700px;top:3528px;color:var(--white);font-size:12px;line-height:1.6}
.hours h4{font-size:14px;font-weight:500;margin-bottom:2px}
.hours span{color:#dbe3f3}

/* blog */
.post{position:absolute;top:3840px;width:418px;height:322px;background:#f2f3f6;overflow:hidden}
.post .meta{position:absolute;left:23px;top:40px;font-size:11px;color:var(--teal);line-height:1.6}
.post .meta span{display:block;color:var(--muted)}
.post h3{position:absolute;left:23px;top:108px;width:250px;font-size:17px;font-weight:500;line-height:1.4}
.post p{position:absolute;left:23px;top:170px;width:240px;font-size:12px;color:var(--muted);line-height:1.6}
.post .more{position:absolute;left:23px;top:277px;font-size:11px;color:var(--navy);border-bottom:1px solid var(--navy);padding-bottom:2px}
.post .thumb{position:absolute;right:0;top:0;width:143px;height:322px}

/* footer */
.footer{top:4305px;left:0;width:1200px;height:317px;background:var(--footer);color:var(--white)}
.footer h4{font-weight:500;font-size:16px}
.footer ul{list-style:none;font-size:12px;line-height:27px}
.contact-row{display:flex;align-items:center;gap:14px;font-size:12px;margin-bottom:13px}
.contact-row i{width:27px;height:27px;border-radius:50%;background:var(--teal);display:flex;align-items:center;justify-content:center}
</style>
</head>
<body>

<!-- top bar -->
<div class="abs topbar">
  <div class="abs social" style="left:160px;top:12px"><span></span><span></span><span></span><span></span></div>
  <div class="abs" style="left:682px;top:9px;display:flex;align-items:center;gap:8px">
    <svg width="12" height="12" viewBox="0 0 24 24"><path d="M6.6 10.8a15 15 0 0 0 6.6 6.6l2.2-2.2a1 1 0 0 1 1-.25 11.4 11.4 0 0 0 3.6.6 1 1 0 0 1 1 1V20a1 1 0 0 1-1 1A17 17 0 0 1 3 4a1 1 0 0 1 1-1h3.5a1 1 0 0 1 1 1c0 1.25.2 2.45.6 3.6a1 1 0 0 1-.25 1z" fill="#1f3a7f"/></svg>
    + 1 555 014 2290
  </div>
  <div class="abs" style="left:826px;top:9px;display:flex;align-items:center;gap:10px">
    <svg width="14" height="10" viewBox="0 0 14 10"><rect width="14" height="10" fill="#1f3a7f"/><path d="M0 0l7 5 7-5" stroke="#fff" fill="none"/></svg>
    info@harrowfielddental.com
  </div>
</div>

<!-- hero -->
<div class="photo hero-photo" role="img" aria-label="Smiling patient in a dental chair during a check-up"></div>
<div class="abs nav">
  <div class="abs brand" style="left:160px;top:24px">Harrowfield<small>— DENTISTRY —</small></div>
  <div class="abs nav-links" style="left:436px;top:35px"><span>Home</span><span>About Us</span><span>Services</span><span>Dentists</span><span>Contact Us</span></div>
  <div class="btn" style="left:877px;top:24px;width:161px;height:42px;font-size:13px">Book Appointment</div>
</div>
<div class="abs hero-ring"></div>
<div class="abs hero-circle">
  <h1>High Quality and<strong>Painless Dentistry</strong></h1>
  <p>If you are in need of high-quality, professional and friendly dental care, look no further than our clinic.</p>
</div>
<div class="btn" style="left:760px;top:466px;width:161px;height:41px">Learn More</div>
<svg class="abs" style="left:0;top:640px" width="1200" height="90" viewBox="0 0 1200 90">
  <path d="M0 55 C300 85 700 0 1200 15 L1200 90 L0 90Z" fill="#5aacbc"/>
  <path d="M0 60 C320 95 720 20 1200 32 L1200 90 L0 90Z" fill="#fff"/>
</svg>

<!-- about -->
<div class="photo" style="left:520px;top:690px;width:680px;height:560px;background:linear-gradient(90deg,#ffffff 0%,#e9eef2 30%,#d5dde4 65%,#b99682 100%)" role="img" aria-label="Dentist in white coat examining a smiling patient"></div>
<div class="abs" style="left:160px;top:810px;width:370px">
  <div class="eyebrow"><span>About Us</span><span class="mark" role="img" aria-label="Small leaf accent"></span></div>
  <h2 style="margin-top:14px">Professionals and Personalized Dental Excellence</h2>
  <p class="lead" style="margin-top:14px;color:var(--ink)">Welcome to our BrightpathChapters dedicated to empowering pet owners with valuable knowledge and resources.</p>
  <p class="lead" style="margin-top:14px;color:var(--ink)">Welcome to our BrightpathChapters dedicated to empowering pet owners with valuable knowledge and resources.</p>
</div>
<div class="btn" style="left:160px;top:1126px;width:161px;height:41px">Learn More</div>

<!-- services -->
<svg class="abs" style="left:0;top:1218px" width="1200" height="60" viewBox="0 0 1200 60">
  <path d="M0 10 C250 60 700 0 1200 20 L1200 60 L0 60Z" fill="#5aacbc"/>
  <path d="M0 40 C300 60 700 15 1200 40 L1200 60 L0 60Z" fill="#1f3a7f"/>
</svg>
<div class="abs" style="left:0;top:1270px;width:1200px;height:700px;background:var(--navy)"></div>
<div class="abs center" style="top:1315px;color:var(--white)">
  <div class="eyebrow light"><span>Our Services</span><span class="mark" role="img" aria-label="Small leaf accent"></span></div>
  <h2 style="color:var(--white);margin-top:6px">Complete Care for Every Smile</h2>
  <p class="lead" style="color:#dbe3f3;width:540px;margin:10px auto 0;line-height:1.3">Welcome to our BrightpathChapters dedicated to empowering pet owners with valuable knowledge and resources.</p>
</div>
<svg class="abs" style="left:142px;top:1630px" width="14" height="26" viewBox="0 0 14 26"><path d="M12 2 2 13l10 11" stroke="#fff" stroke-width="2" fill="none"/></svg>
<svg class="abs" style="left:1040px;top:1630px" width="14" height="26" viewBox="0 0 14 26"><path d="M2 2l10 11L2 24" stroke="#fff" stroke-width="2" fill="none"/></svg>

<div class="service-card" style="left:228px"><h3>Implants</h3><p>It is a long established fact that a will be distracted.</p></div>
<div class="service-photo" style="left:249px;background:linear-gradient(140deg,#e6d2c4,#9bb3cf)" role="img" aria-label="Patient receiving dental implant treatment"></div>
<div class="btn btn-navy" style="left:269px;top:1749px;width:130px;height:34px">View Details</div>

<div class="service-card" style="left:492px"><h3>Cosmetic Dentistry</h3><p>It is a long established fact that a will be distracted.</p></div>
<div class="service-photo" style="left:513px;background:linear-gradient(140deg,#b8cde4,#6c85b8)" role="img" aria-label="Patient during a cosmetic dental procedure"></div>
<div class="btn btn-navy" style="left:534px;top:1749px;width:130px;height:34px">View Details</div>

<div class="service-card" style="left:757px"><h3>Emergency Services</h3><p>It is a long established fact that a will be distracted.</p></div>
<div class="service-photo" style="left:778px;background:linear-gradient(140deg,#e9e2dc,#a8b4c2)" role="img" aria-label="Smiling man after emergency dental care"></div>
<div class="btn btn-navy" style="left:798px;top:1749px;width:130px;height:34px">View Details</div>

<div class="abs center service-more"><span class="label">Also offered:</span><span>Dental Hygiene</span><span>Restorations</span><span>Dentures</span></div>

<div class="btn" style="left:520px;top:1878px;width:161px;height:41px">View All Services</div>
<svg class="abs" style="left:0;top:1940px" width="1200" height="80" viewBox="0 0 1200 80">
  <path d="M0 0 L1200 0 L1200 30 C800 70 300 20 0 45Z" fill="#5aacbc"/>
  <path d="M0 0 L1200 0 L1200 10 C800 55 300 5 0 30Z" fill="#1f3a7f"/>
</svg>

<!-- team -->
<div class="abs center" style="top:2055px">
  <div class="eyebrow"><span>Meet Our Dental Team</span><span class="mark" role="img" aria-label="Small leaf accent"></span></div>
  <h2 style="margin-top:6px">Committed to Your Smile</h2>
  <p class="lead" style="width:540px;margin:10px auto 0">Welcome to our BrightpathChapters dedicated to empowering pet owners with valuable knowledge and resources.</p>
</div>
<div class="member" style="left:160px"><div class="avatar" style="background:linear-gradient(160deg,#dfe6ef,#7fa6d2)" role="img" aria-label="Portrait of a female dentist"></div><h3>Dr. Clara Whitmore</h3><p>Lead Dentist</p></div>
<div class="member" style="left:386px"><div class="avatar" style="background:linear-gradient(160deg,#d6d9dd,#9aa5b3)" role="img" aria-label="Portrait of a male dentist"></div><h3>Dr. Clara Whitmore</h3><p>Lead Dentist</p></div>
<div class="member" style="left:612px"><div class="avatar" style="background:linear-gradient(160deg,#5fc1e0,#2d86c0)" role="img" aria-label="Portrait of a female dentist with glasses"></div><h3>Dr. Clara Whitmore</h3><p>Lead Dentist</p></div>
<div class="member" style="left:838px"><div class="avatar" style="background:linear-gradient(160deg,#eef0f2,#b7c0cb)" role="img" aria-label="Portrait of a male dentist in a white coat"></div><h3>Dr. Clara Whitmore</h3><p>Lead Dentist</p></div>
<div class="btn" style="left:520px;top:2476px;width:161px;height:41px">View All Team</div>

<!-- testimonial -->
<svg class="abs" style="left:0;top:2565px" width="1200" height="60" viewBox="0 0 1200 60">
  <path d="M0 60 L0 55 C400 50 800 0 1200 5 L1200 60Z" fill="#5aacbc"/>
  <path d="M0 60 L0 58 C400 58 800 15 1200 22 L1200 60Z" fill="#e8ecf4"/>
</svg>
<div class="abs" style="left:0;top:2620px;width:1200px;height:520px;background:var(--band)"></div>
<div class="abs" style="left:437px;top:2690px;width:620px">
  <div class="eyebrow"><span>Our Testimonial</span><span class="mark" role="img" aria-label="Small leaf accent"></span></div>
  <h2 style="margin-top:10px">Pleasing Patients Is Our Greatest Achievement</h2>
</div>
<div class="photo" style="left:192px;top:2850px;width:200px;height:200px;border-radius:50%;background:linear-gradient(160deg,#f1efed,#3b3433)" role="img" aria-label="Portrait of a smiling patient"></div>
<div class="abs" style="left:436px;top:2840px;font-size:13px;font-weight:500;line-height:1.45">Nora Lindqvist<br>Meridel Holdings Ltd.</div>
<svg class="abs" style="left:608px;top:2843px" width="38" height="30" viewBox="0 0 38 30"><path d="M0 30V16C0 6 6 1 15 0v6c-5 1-7 4-7 9h7v15zm21 0V16c0-10 6-15 15-16v6c-5 1-7 4-7 9h7v15z" fill="#8fc8d3"/></svg>
<p class="abs lead" style="left:436px;top:2888px;width:600px;line-height:1.5;color:#555">There are many variations of passages of Lorem Ipsum available, but the majority have suffered alteration in some form, by injected humour, or randomised words which don't look even slightly believable. If you are going to use a passage of Lorem Ipsum, you need to be sure there isn't anything embarrassing hidden in the middle of text. All the Lorem Ipsum generators on the Internet tend to repeat predefined chunks as necess.</p>
<div class="btn" style="left:438px;top:3015px;width:178px;height:41px">View All Testimonial</div>

<!-- appointment -->
<svg class="abs" style="left:0;top:3095px" width="1200" height="60" viewBox="0 0 1200 60">
  <path d="M0 60 L0 40 C400 0 800 5 1200 20 L1200 60Z" fill="#1f3a7f"/>
</svg>
<div class="abs" style="left:0;top:3150px;width:1200px;height:470px;background:var(--navy)"></div>
<div class="photo" style="left:678px;top:3162px;width:522px;height:350px;border-radius:250px 0 0 250px;background:linear-gradient(110deg,#c29a7f,#e7d3c4 40%,#9db0c4 70%,#dfe5ea)" role="img" aria-label="Patient smiling during a dental exam"></div>
<div class="abs" style="left:182px;top:3190px">
  <div class="eyebrow light"><span>Contact</span><span class="mark" role="img" aria-label="Small leaf accent"></span></div>
  <h2 style="color:var(--white);font-size:27px;margin-top:4px">Make An Appointment</h2>
</div>
<div class="field" style="left:182px;top:3292px;width:178px">Name*</div>
<div class="field" style="left:400px;top:3292px;width:178px">Company Name</div>
<div class="field" style="left:182px;top:3354px;width:178px">Phone</div>
<div class="field" style="left:400px;top:3354px;width:178px">Email Address*</div>
<div class="field" style="left:182px;top:3418px;width:396px;height:74px">Your Message</div>
<div class="btn" style="left:182px;top:3532px;width:205px;height:41px;font-size:12px">SUBMIT</div>
<div class="abs hours">
  <h4>Opening Hours</h4>
  Mon – Fri <span>8:00 am – 6:00 pm</span> &nbsp;·&nbsp; Sat <span>9:00 am – 2:00 pm</span> &nbsp;·&nbsp; Sun <span>Closed</span>
</div>
<svg class="abs" style="left:0;top:3580px" width="1200" height="80" viewBox="0 0 1200 80">
  <path d="M0 0 L1200 0 L1200 20 C800 10 350 70 0 50Z" fill="#5aacbc"/>
  <path d="M0 0 L1200 0 L1200 5 C800 0 350 55 0 35Z" fill="#1f3a7f"/>
  <path d="M0 50 C350 70 800 10 1200 20 L1200 80 L0 80Z" fill="#fff"/>
</svg>

<!-- blog -->
<div class="abs center" style="top:3680px">
  <div class="eyebrow"><span>Our Latest Blog</span><span class="mark" role="img" aria-label="Small leaf accent"></span></div>
  <h2 style="margin-top:6px">Latest Posts &amp; Articles</h2>
  <p class="lead" style="width:540px;margin:10px auto 0;line-height:1.3">Welcome to our BrightpathChapters dedicated to empowering pet owners with valuable knowledge and resources.</p>
</div>
<article class="post" style="left:161px">
  <div class="meta">HARROWFIELD<span>Mar 25, 2025</span></div>
  <h3>How to Choose the Best<br>In&#8209;Home Pet Care Service</h3>
  <p>Consectetuer fringilla aenean sagittis potenti ullamcorper nam porta feugiat. Ante urna congue feugiat efficitur vel duis.</p>
  <div class="more">LEARN MORE ›</div>
  <div class="thumb" style="background:linear-gradient(160deg,#c9a38a,#7b8cb0)" role="img" aria-label="Patient during dental treatment"></div>
</article>
<article class="post" style="left:619px">
  <div class="meta">HARROWFIELD<span>Mar 25, 2025</span></div>
  <h3>How to Choose the Best<br>In&#8209;Home Pet Care Service</h3>
  <p>Consectetuer fringilla aenean sagittis potenti ullamcorper nam porta feugiat. Ante urna congue feugiat efficitur vel duis.</p>
  <div class="more">LEARN MORE ›</div>
  <div class="thumb" style="background:linear-gradient(160deg,#e9ecef,#3a6fb5)" role="img" aria-label="Dentist treating a patient"></div>
</article>
<div class="btn" style="left:520px;top:4208px;width:161px;height:41px;font-size:12px">VIEW ALL BLOG</div>

<!-- footer -->
<svg class="abs" style="left:0;top:4275px" width="1200" height="40" viewBox="0 0 1200 40">
  <path d="M0 40 L0 30 C400 40 800 0 1200 5 L1200 40Z" fill="#5aacbc"/>
  <path d="M0 40 L0 38 C400 40 800 12 1200 18 L1200 40Z" fill="#0e1a30"/>
</svg>
<footer class="abs footer">
  <div class="abs brand" style="left:160px;top:70px">Harrowfield<small>— DENTISTRY —</small></div>
  <p class="abs" style="left:160px;top:147px;width:290px;font-size:11px;line-height:1.55">It is a long established fact that a reader will be distracted by the readable content of a page when looking at its layout.</p>
  <div class="abs social" style="left:160px;top:210px"><span style="background:var(--teal)"></span><span style="background:var(--teal)"></span><span style="background:var(--teal)"></span></div>
  <h4 class="abs" style="left:576px;top:60px">Quick Links</h4>
  <ul class="abs" style="left:576px;top:98px"><li>Home</li><li>About Us</li><li>Services</li><li>Team</li><li>Contact Us</li></ul>
  <h4 class="abs" style="left:831px;top:60px">Contact Us</h4>
  <div class="abs" style="left:831px;top:100px">
    <div class="contact-row"><i><svg width="12" height="12" viewBox="0 0 24 24"><path d="M6.6 10.8a15 15 0 0 0 6.6 6.6l2.2-2.2a1 1 0 0 1 1-.25 11.4 11.4 0 0 0 3.6.6 1 1 0 0 1 1 1V20a1 1 0 0 1-1 1A17 17 0 0 1 3 4a1 1 0 0 1 1-1h3.5a1 1 0 0 1 1 1c0 1.25.2 2.45.6 3.6a1 1 0 0 1-.25 1z" fill="#fff"/></svg></i>+1 555 014 2290</div>
    <div class="contact-row"><i><svg width="13" height="9" viewBox="0 0 14 10"><rect width="14" height="10" fill="#fff"/><path d="M0 0l7 5 7-5" stroke="#5aacbc" fill="none"/></svg></i>harrowfield5521@gmail.com</div>
    <div class="contact-row"><i><svg width="10" height="14" viewBox="0 0 10 14"><path d="M5 0a5 5 0 0 1 5 5c0 4-5 9-5 9S0 9 0 5a5 5 0 0 1 5-5z" fill="#fff"/><circle cx="5" cy="5" r="2" fill="#5aacbc"/></svg></i>122, Lorem ipsum dolrd</div>
  </div>
  <div class="abs" style="left:160px;top:260px;width:880px;border-top:1px solid rgba(255,255,255,.2)"></div>
  <p class="abs" style="left:0;width:1200px;top:282px;text-align:center;font-size:12px">Copyright © 2025harrowfield. All rights reserved.</p>
</footer>

</body>
</html>
```